New Business Card Design Project

I need a design for business cards, i am an electrical business called "Corvane Electrical and Communications" i need the cards to be double sided with the company logo on the back (attached) the front needs to say my company name, web site, email address, telephone number, and ABN number and electrical license number. I am open to different arrangements of the information but would like the background to be incorporating something electrical or something that looks smart. open to all additional ideas also.

The company colours are orange and grey see logo attached.

Business Name: Corvane Electrical and Communications
Website: corvaneelectricalandcomms.example.com.au
Email: brent@corvaneelectricalandcomms.example.com.au
Telephone(mobile): 0481209736
ABN: 71208349162
Lic No: 418273D

Target Market(s)

Business entities, Project Managers, Accounts, Clients

Industry/Entity Type

Electrician

Contact Information for Business Card

I need a design for business cards, i am an electrical business called "Corvane Electrical and Communications" i need the cards to be double sided with the company logo on the back (attached) the front needs to say my company name

Font styles to use
Serif
Sans Serif

Colors
f37122
5c5c5c

Requirements
Must have
• Must have the Logo on the back open to different ways of it being on the back but had in mind to keep it central but again open to other options
Nice to have
• A real modern cool background that is eye catching yet contemporary
Should not have
• No backgrounds of a light bulb or plug or anything like that

```html
<!DOCTYPE html>
<html lang="en">
<head>
<meta charset="utf-8">
<title>Corvane Electrical and Communications – Business Cards</title>
<link rel="stylesheet" href="https://fonts.googleapis.com/css2?family=Questrial&display=swap">
<style>
  :root {
    --orange: #f5a81c;
    --brand-orange: #f37122;
    --grey: #5c5c5c;
    --black: #050505;
    --white: #ffffff;
    --backdrop: #2b2b2b;
  }
  * { margin: 0; padding: 0; box-sizing: border-box; }
  html, body {
    width: 1200px;
    height: 900px;
    overflow: hidden;
    background: var(--backdrop);
    font-family: "Questrial", "Century Gothic", sans-serif;
  }
  .canvas {
    position: relative;
    width: 1200px;
    height: 900px;
  }
  .card {
    position: absolute;
    width: 560px;
    height: 320px;
    overflow: hidden;
    box-shadow: 0 18px 40px rgba(0,0,0,0.55);
  }
  .card--back {
    left: 70px;
    top: 90px;
    background: var(--black);
  }
  .card--front {
    left: 570px;
    top: 490px;
    background: var(--black);
  }

  /* wordmark */
  .wordmark {
    position: absolute;
    left: 0;
    right: 0;
    text-align: center;
    color: var(--orange);
    line-height: 1;
  }
  .wordmark__name {
    display: block;
    font-size: 64px;
    letter-spacing: 4px;
  }
  .wordmark__line {
    display: block;
    margin-top: 8px;
    font-size: 15px;
    letter-spacing: 2px;
  }
  .card--back .wordmark { top: 100px; }

  .back-web {
    position: absolute;
    right: 28px;
    bottom: 26px;
    color: var(--white);
    font-size: 15px;
    letter-spacing: 0.3px;
  }

  /* front card */
  .front-top {
    position: absolute;
    left: 0;
    top: 0;
    width: 100%;
    height: 168px;
    background: var(--white);
  }
  .card--front .wordmark { top: 28px; }
  .card--front .wordmark__name { font-size: 52px; }
  .card--front .wordmark__line { font-size: 13px; }
  .licence {
    position: absolute;
    left: 0;
    right: 0;
    top: 126px;
    text-align: center;
    font-size: 15px;
    color: var(--orange);
  }
  .licence__value { color: var(--grey); }

  .contact {
    position: absolute;
    right: 28px;
    top: 176px;
    text-align: right;
    color: var(--white);
    font-size: 12.5px;
    line-height: 1.45;
  }
  .contact__name {
    font-size: 22px;
    color: var(--orange);
    letter-spacing: 0.5px;
    line-height: 1.1;
  }
  .contact__role {
    font-size: 11px;
    letter-spacing: 0.5px;
    margin-bottom: 4px;
  }
  .contact__label { color: var(--orange); }
</style>
</head>
<body>
<main class="canvas">

  <section class="card card--back" aria-label="Card back">
    <div class="wordmark">
      <span class="wordmark__name">CORVANE</span>
      <span class="wordmark__line">ELECTRICAL &amp; COMMUNICATIONS</span>
    </div>
    <p class="back-web">www.corvaneelectricalandcomms.example.com.au</p>
  </section>

  <section class="card card--front" aria-label="Card front">
    <div class="front-top"></div>
    <div class="wordmark">
      <span class="wordmark__name">CORVANE</span>
      <span class="wordmark__line">ELECTRICAL &amp; COMMUNICATIONS</span>
    </div>
    <p class="licence">Lic No: <span class="licence__value">418273D</span></p>

    <div class="contact">
      <p class="contact__name">ROWAN ASHCROFT</p>
      <p class="contact__role">DIRECTOR</p>
      <p><span class="contact__label">ABN:</span> 71208349162</p>
      <p><span class="contact__label">P:</span> 0481 209 736</p>
      <p><span class="contact__label">E:</span> brent@corvaneelectricalandcomms.example.com.au</p>
      <p><span class="contact__label">W:</span> www.corvaneelectricalandcomms.example.com.au</p>
    </div>
  </section>

</main>
</body>
</html>
```